Business Card Design for Property Development Company Director

I am looking for a professional and unforgettable business card design for our Director of our Property Development Company.
Please see attached .pptx file to find out what information to include. You don't have to follow the exact format shown in the file - I am interested to see your creative flair using the information provided.

```html
<!DOCTYPE html>
<html lang="en">
<head>
<meta charset="utf-8">
<title>Kestrel Property Group – Business Card</title>
<link href="https://fonts.googleapis.com/css2?family=Open+Sans:wght@600;700&family=Roboto:wght@400;500;700&display=swap" rel="stylesheet">
<style>
  :root {
    --stage: #d6d6d8;
    --card-dark: #1e1e20;
    --card-light: #ffffff;
    --brand-blue: #1458ad;
    --brand-grey: #5f5f62;
    --ink: #111111;
    --muted: #8a8a8c;
  }
  * { box-sizing: border-box; margin: 0; padding: 0; }
  html, body { width: 1200px; height: 1200px; overflow: hidden; }
  body {
    background: var(--stage);
    font-family: "Roboto", Arial, sans-serif;
    display: flex;
    flex-direction: column;
    align-items: center;
    justify-content: center;
    gap: 50px;
  }
  .card {
    width: 900px;
    height: 514px;
    border-radius: 28px;
    position: relative;
    overflow: hidden;
    box-shadow: 0 6px 20px rgba(0,0,0,0.18);
  }
  .card--back { background: var(--card-dark); }
  .card--front { background: var(--card-light); }

  /* Wordmark */
  .wordmark { display: flex; align-items: center; gap: 22px; }
  .wordmark__square { width: 78px; height: 78px; background: var(--brand-grey); flex: none; }
  .wordmark__text { display: flex; flex-direction: column; line-height: 1; }
  .wordmark__name {
    font-family: "Roboto", Arial, sans-serif;
    font-weight: 700;
    font-size: 78px;
    color: var(--brand-blue);
    letter-spacing: 1px;
  }
  .wordmark__sub {
    font-family: "Roboto", Arial, sans-serif;
    font-weight: 500;
    font-size: 26px;
    color: var(--brand-blue);
    letter-spacing: 9px;
    margin-top: 6px;
  }

  /* Back */
  .back__tagline {
    position: absolute; top: 70px; left: 0; right: 0;
    text-align: center;
    font-family: "Open Sans", Verdana, sans-serif;
    font-weight: 700;
    font-size: 27px;
    line-height: 1.2;
    color: var(--brand-blue);
  }
  .back__logo {
    position: absolute; top: 190px; left: 0; right: 0;
    display: flex; justify-content: center;
  }
  .back__footer {
    position: absolute; bottom: 56px; left: 0; right: 0;
    text-align: center;
    font-size: 24px;
    color: var(--muted);
  }
  .back__footer .accent { color: var(--brand-blue); }

  /* Front */
  .front__logo { position: absolute; top: 60px; left: 60px; }
  .contact { position: absolute; left: 470px; top: 290px; }
  .contact__name { font-weight: 700; font-size: 36px; color: var(--brand-blue); }
  .contact__role { font-size: 20px; color: var(--ink); margin-bottom: 22px; }
  .contact__row {
    display: flex; align-items: center; gap: 14px;
    font-size: 24px; color: var(--ink); margin-bottom: 6px;
  }
  .contact__row svg { width: 24px; height: 24px; flex: none; }
  .contact__web strong { color: var(--brand-blue); font-weight: 700; }
  .contact__licence { font-size: 20px; color: var(--brand-grey); margin-top: 10px; }
  .contact__licence .accent { color: var(--brand-blue); font-weight: 500; }
</style>
</head>
<body>

  <section class="card card--back">
    <p class="back__tagline">Property Development<br>&amp; Site Acquisition Specialists</p>
    <div class="back__logo">
      <div class="wordmark">
        <span class="wordmark__square"></span>
        <div class="wordmark__text">
          <span class="wordmark__name">KESTREL</span>
          <span class="wordmark__sub">PROPERTY GROUP</span>
        </div>
      </div>
    </div>
    <p class="back__footer">Ask me about our <span class="accent">INVESTMENT &amp; PARTNERSHIP</span> opportunities</p>
  </section>

  <section class="card card--front">
    <div class="front__logo">
      <div class="wordmark">
        <span class="wordmark__square"></span>
        <div class="wordmark__text">
          <span class="wordmark__name">KESTREL</span>
          <span class="wordmark__sub">PROPERTY GROUP</span>
        </div>
      </div>
    </div>

    <div class="contact">
      <p class="contact__name">Daniel Morrow</p>
      <p class="contact__role">Director</p>
      <p class="contact__row">
        <svg viewBox="0 0 24 24" aria-hidden="true"><path fill="#1458ad" d="M6.6 10.8a15 15 0 0 0 6.6 6.6l2.2-2.2a1 1 0 0 1 1-.25 11.4 11.4 0 0 0 3.6.57 1 1 0 0 1 1 1V20a1 1 0 0 1-1 1A17 17 0 0 1 3 4a1 1 0 0 1 1-1h3.5a1 1 0 0 1 1 1c0 1.25.2 2.45.57 3.6a1 1 0 0 1-.25 1z"/></svg>
        0400 123 456
      </p>
      <p class="contact__row">
        <svg viewBox="0 0 24 24" aria-hidden="true"><rect x="2" y="5" width="20" height="14" rx="1.5" fill="none" stroke="#1458ad" stroke-width="2"/><path d="M3 6l9 7 9-7" fill="none" stroke="#1458ad" stroke-width="2"/></svg>
        daniel@kestrelpg.com.au
      </p>
      <p class="contact__row contact__web">
        <svg viewBox="0 0 24 24" aria-hidden="true"><g fill="none" stroke="#1458ad" stroke-width="1.8"><circle cx="12" cy="12" r="9.5"/><ellipse cx="12" cy="12" rx="4.5" ry="9.5"/><path d="M2.5 12h19M4 7h16M4 17h16"/></g></svg>
        <span>www.<strong>kestrelpg.com</strong>.au</span>
      </p>
      <p class="contact__licence">Real Estate Lic: <span class="accent">4100001 &amp; 4100002</span></p>
    </div>
  </section>

</body>
</html>
```